Diverse, up-scale salon needs eye-catching, unique business cards.

We are looking for a unique business card design for our stylist but that can also be multi functional and used for appointment reminder and referrals. I will need a design in a format that I can modify names and titles going forward. In the past we have had a dark background with the logo on one side, and stylist and contact information on the other but we are open to all ideas. I have included our mission statement as well as branded colors below. The statement doesn't need to go on the card, it's just a reference for target market. We need space for the stylists name, title, instagram handle and then the salons phone number, website and address. I am also open to adding a spot for a qr code linked to the stylist instagram or the salon booking link.

primary brand colors:
#333333 #233415 #36502a #93874a #000000
Mission statement:
Vessolin Hair Studio, a high-end salon located in the lively Downtown Farmington, Michigan, is committed to providing exceptional services in a welcoming and relaxed environment to meet the needs of our diverse clientele.
Our salon specializes in contemporary custom haircuts, coloring, extensions, and barbering and beard grooming services. Our team of skilled stylists is passionate and inventive in their hair styling techniques. At the heart of our salon are values centered on quality, innovation, creativity, and above all, comfort. These core values are evident in every appointment across our customizable array of services.
Our goal is to establish a benchmark for exceptional hair care for every human.
Website: www.vessolinhairstudio.example
instagram: @vessolinhairstudio
address: 41782 Pelham Crest Rd, Farmington MI
phone: 248-613-4087

Industry/Entity Type

Hair Salon

Contact Information for Business Card

Stylist name, title, phone, instagram, website, address, (optional qr code)

Requirements
Should not have
• Does not need mission statement on the card.

```html
<!DOCTYPE html>
<html lang="en">
<head>
<meta charset="utf-8">
<title>Vessolin Hair Studio – Business Card</title>
<link rel="stylesheet" href="https://fonts.googleapis.com/css2?family=Montserrat:wght@400;600&display=swap">
<style>
  :root {
    --page: #e4e4e1;
    --olive: #93874a;
    --paper: #ffffff;
    --swoosh: #2b2b2b;
    --ink-light: #ffffff;
  }
  * { box-sizing: border-box; margin: 0; padding: 0; }
  html, body {
    width: 1200px; height: 900px; overflow: hidden;
    background: var(--page);
    font-family: "Montserrat", sans-serif;
  }
  .canvas {
    position: relative; width: 1200px; height: 900px;
  }
  .card {
    position: absolute; left: 280px; width: 640px; height: 366px;
    overflow: hidden;
  }
  .card--front { top: 70px; background: var(--olive); }
  .card--back { top: 464px; background: var(--olive); }

  .card__art { position: absolute; inset: 0; width: 640px; height: 366px; }

  .brand {
    position: absolute; display: flex; align-items: center; gap: 14px;
    font-weight: 600; letter-spacing: 0.08em; text-transform: uppercase;
  }
  .brand__dot {
    width: 18px; height: 18px; border-radius: 50%;
    border: 2px solid currentColor; flex: none;
  }
  .card--front .brand {
    color: var(--ink-light); font-size: 26px;
    left: 0; right: 0; top: 0; bottom: 0; justify-content: center;
  }
  .card--back .brand {
    color: var(--olive); font-size: 17px;
    left: 345px; top: 112px;
  }

  .contact {
    position: absolute; left: 44px; top: 196px;
    color: var(--ink-light); font-size: 13px; line-height: 1.45;
  }
  .contact__address { margin-bottom: 10px; }
  .contact__list { list-style: none; }
  .contact__item { display: flex; align-items: center; gap: 8px; margin-bottom: 3px; }
  .contact__icon {
    width: 16px; height: 16px; border-radius: 50%; background: var(--ink-light);
    display: flex; align-items: center; justify-content: center; flex: none;
  }
  .contact__icon svg { width: 10px; height: 10px; }
</style>
</head>
<body>
<main class="canvas">

  <section class="card card--front" aria-label="Card front">
    <div class="brand"><span class="brand__dot"></span>Vessolin Hair Studio</div>
  </section>

  <section class="card card--back" aria-label="Card back">
    <svg class="card__art" viewBox="0 0 640 366" aria-hidden="true">
      <path d="M300 0 L640 0 L640 300 C520 292 330 232 300 112 C290 72 292 32 300 0 Z" fill="var(--paper)"/>
      <path d="M300 112 C330 232 520 292 640 300 L640 322 C500 318 318 252 300 112 Z" fill="var(--swoosh)"/>
      <path d="M300 112 C322 250 500 316 640 322 L640 330 C500 326 312 262 300 112 Z" fill="var(--paper)"/>
    </svg>

    <div class="brand"><span class="brand__dot"></span>Vessolin Hair Studio</div>

    <div class="contact">
      <p class="contact__address">41782 Pelham Crest Rd,<br>Farmington MI</p>
      <ul class="contact__list">
        <li class="contact__item">
          <span class="contact__icon">
            <svg viewBox="0 0 10 10"><path d="M2 1 L4 1 L4.5 3 L3.4 3.8 C3.9 5 5 6.1 6.2 6.6 L7 5.5 L9 6 L9 8 C5 8.5 1.5 5 2 1 Z" fill="var(--olive)"/></svg>
          </span>248-613-4087
        </li>
        <li class="contact__item">
          <span class="contact__icon">
            <svg viewBox="0 0 10 10" fill="none" stroke="var(--olive)" stroke-width="1"><circle cx="5" cy="5" r="4"/><ellipse cx="5" cy="5" rx="1.8" ry="4"/><path d="M1 5 H9"/></svg>
          </span>www.vessolinhairstudio.example
        </li>
        <li class="contact__item">
          <span class="contact__icon"></span>@vessolinhairstudio
        </li>
      </ul>
    </div>
  </section>

</main>
</body>
</html>
```